Create a memorable Stationary for Security Software Company

Velbrantix is the worldwide leader in securing the Internet. Making Internet communications and critical data secure, reliable and available everywhere has been and continues to be our ongoing vision. We are committed to staying focused on real customer needs and to developing new and innovative security solutions that redefine the security landscape.

Industry/Entity Type

Internet

Font styles to use
Serif
Sans Serif
Script

Colors
0792cd
33a6d7
85cae6

```html
<!DOCTYPE html>
<html lang="en">
<head>
<meta charset="utf-8">
<title>Velbrantix Business Card</title>
<link rel="stylesheet" href="https://fonts.googleapis.com/css2?family=PT+Sans:wght@400;700&display=swap">
<style>
  :root {
    --page-bg: #e6e1da;
    --card-bg: #f4f2ef;
    --card-edge: #d6d1ca;
    --brand-blue: #0792cd;
    --mid-blue: #33a6d7;
    --light-blue: #85cae6;
    --deep-blue: #1c6a8e;
    --wave-dark: #256f92;
    --text-dark: #3b4046;
    --text-soft: #5c6670;
  }
  html, body {
    margin: 0;
    padding: 0;
    width: 1200px;
    height: 970px;
    overflow: hidden;
    background: var(--page-bg);
  }
  .canvas {
    position: relative;
    width: 1200px;
    height: 970px;
    font-family: "PT Sans", Arial, sans-serif;
  }
  .business-card {
    position: absolute;
    left: 100px;
    top: 200px;
    width: 1000px;
    height: 570px;
    border-radius: 30px;
    background: var(--card-bg);
    border: 1px solid var(--card-edge);
    box-shadow: 0 12px 40px rgba(60, 50, 40, 0.18);
    overflow: hidden;
  }
  .brand-block {
    position: absolute;
    left: 80px;
    top: 250px;
    display: flex;
    align-items: center;
    gap: 18px;
  }
  .brand-dot {
    width: 46px;
    height: 46px;
    border-radius: 50%;
    background: var(--mid-blue);
  }
  .brand-name {
    font-size: 52px;
    font-weight: 700;
    color: var(--mid-blue);
    letter-spacing: 0.5px;
  }
  .divider {
    position: absolute;
    left: 512px;
    top: 118px;
    width: 2px;
    height: 312px;
    background: var(--deep-blue);
    opacity: 0.7;
  }
  .contact-block {
    position: absolute;
    left: 566px;
    top: 118px;
    color: var(--text-dark);
  }
  .person-name {
    margin: 0;
    font-size: 35px;
    font-weight: 700;
    color: var(--deep-blue);
    line-height: 1;
  }
  .person-role {
    margin: 4px 0 0;
    font-size: 26px;
    line-height: 1.1;
  }
  .address {
    margin: 44px 0 0;
    font-size: 27px;
    line-height: 1.3;
    font-style: normal;
  }
  .contact-list {
    list-style: none;
    margin: 14px 0 0;
    padding: 0;
    font-size: 27px;
    line-height: 1;
  }
  .contact-list li {
    display: flex;
    align-items: center;
    gap: 10px;
    height: 36px;
  }
  .contact-icon {
    width: 26px;
    height: 26px;
    flex: none;
  }
  .wave-band {
    position: absolute;
    left: 0;
    bottom: 0;
    width: 1000px;
    height: 110px;
  }
  .website {
    position: absolute;
    left: 566px;
    top: 518px;
    font-size: 25px;
    color: var(--text-soft);
    letter-spacing: 0.5px;
  }
</style>
</head>
<body>
<div class="canvas">
  <div class="business-card">
    <div class="brand-block">
      <div class="brand-dot"></div>
      <div class="brand-name">Velbrantix</div>
    </div>

    <div class="divider"></div>

    <div class="contact-block">
      <h1 class="person-name">Employee Name</h1>
      <p class="person-role">Owner</p>
      <address class="address">0000 Youe Address,2nd Ste.<br>Larkmont, Texas 1234</address>
      <ul class="contact-list">
        <li>
          <svg class="contact-icon" viewBox="0 0 26 26" aria-hidden="true">
            <rect width="26" height="26" rx="2" fill="var(--deep-blue)"/>
            <path d="M6 10c0-3 14-3 14 0v2h-3v-2h-8v2H6z" fill="#fff"/>
            <rect x="8" y="13" width="10" height="6" rx="1" fill="#fff"/>
          </svg>
          <span>+000-000-0000</span>
        </li>
        <li>
          <svg class="contact-icon" viewBox="0 0 26 26" aria-hidden="true">
            <rect width="26" height="26" rx="2" fill="var(--deep-blue)"/>
            <rect x="8" y="5" width="10" height="5" fill="#fff"/>
            <rect x="5" y="11" width="16" height="7" rx="1" fill="#fff"/>
            <rect x="8" y="16" width="10" height="5" fill="#fff" stroke="var(--deep-blue)" stroke-width="1"/>
          </svg>
          <span>123 456 7890</span>
        </li>
        <li>
          <svg class="contact-icon" viewBox="0 0 26 26" aria-hidden="true">
            <rect width="26" height="26" rx="2" fill="var(--deep-blue)"/>
            <rect x="5" y="8" width="16" height="11" fill="#fff"/>
            <path d="M5 8l8 6 8-6M5 19l6-5M21 19l-6-5" fill="none" stroke="var(--deep-blue)" stroke-width="1.3"/>
          </svg>
          <span>hello@velbrantix.com</span>
        </li>
      </ul>
    </div>

    <svg class="wave-band" viewBox="0 0 1000 110" preserveAspectRatio="none" aria-hidden="true">
      <path d="M0 55 C250 10 520 -5 1000 40 L1000 110 L0 110 Z" fill="var(--light-blue)" opacity="0.45"/>
      <path d="M0 70 C260 25 560 10 1000 48 L1000 110 L0 110 Z" fill="var(--mid-blue)" opacity="0.55"/>
      <path d="M0 95 C300 70 620 40 1000 85 L1000 110 L0 110 Z" fill="var(--wave-dark)"/>
      <path d="M0 60 C280 15 560 0 1000 44" fill="none" stroke="var(--wave-dark)" stroke-width="3"/>
    </svg>
    <div class="website">www.velbrantix.com</div>
  </div>
</div>
</body>
</html>
```